Varnex Consulting Business card design.

See our website www.varnexconsulting.example which will give you a good idea of what we are about. The font is called 'Play'.

I'd like a standout business card in keeping with the themes and branding on the website

Target Market(s)

professionals. HR directors

Industry/Entity Type

Business

Contact Information for Business Card

Varnex Consulting PO Box 3172 Merrowdale NSW 2291 1300 485 193 Gavin Threlkeld Principal email: career@varnexconsulting.example ABN: 71203948865

Font styles to use
Other font styles liked:
• Play

Requirements
Must have
• Must have same design colours and branding as website.
• On back I'd prefer a list of the things we do which appears below the name at the header on the website

```html
<!DOCTYPE html>
<html lang="en">
<head>
<meta charset="utf-8">
<title>Varnex Consulting – Business Card</title>
<link rel="stylesheet" href="https://fonts.googleapis.com/css2?family=Cinzel:wght@400&family=Open+Sans:wght@400;600&display=swap">
<style>
  :root {
    --brand-red: #b31217;
    --band-grey: #858585;
    --card-white: #ffffff;
    --stage: #e8e5e2;
  }
  * { margin: 0; padding: 0; box-sizing: border-box; }
  html, body { width: 1200px; height: 900px; overflow: hidden; }
  body {
    background: var(--stage);
    position: relative;
    font-family: "Open Sans", Arial, sans-serif;
  }
  .card {
    position: absolute;
    overflow: hidden;
    box-shadow: 0 6px 18px rgba(0,0,0,0.18);
  }
  .card-front {
    left: 78px; top: 34px; width: 588px; height: 364px;
    background: var(--card-white);
  }
  .card-back {
    left: 388px; top: 505px; width: 566px; height: 352px;
    background: var(--brand-red);
  }
  .front-shapes { position: absolute; inset: 0; }
  .wordmark {
    position: absolute;
    color: var(--brand-red);
    font-family: "Cinzel", Georgia, serif;
    font-weight: 400;
    line-height: 1;
  }
  .wordmark-front { left: 0; right: 0; top: 54px; text-align: center; }
  .wordmark .name-main { display: block; font-size: 46px; letter-spacing: 1px; }
  .wordmark .name-sub { display: block; font-size: 25px; letter-spacing: 5px; margin-top: 4px; }
  .contact-list {
    position: absolute; right: 302px; top: 238px;
    color: var(--card-white); font-size: 15px; text-align: right;
    list-style: none;
  }
  .contact-list li { height: 25px; line-height: 25px; display: flex; justify-content: flex-end; align-items: center; gap: 10px; }
  .contact-list .abn { margin-bottom: 15px; }
  .contact-list .abn strong { font-weight: 600; }
  .contact-list svg { width: 12px; height: 12px; fill: var(--card-white); }
  .person {
    position: absolute; left: 330px; top: 232px; color: var(--card-white);
  }
  .person-name { font-size: 19px; font-weight: 600; line-height: 24px; }
  .person-role { font-size: 15px; line-height: 20px; }
  .person-address { font-size: 15px; line-height: 22px; margin-top: 10px; font-style: normal; }
  .wordmark-back {
    color: var(--card-white);
    right: 32px; top: 224px; text-align: center;
  }
  .wordmark-back .name-main { font-size: 60px; }
  .wordmark-back .name-sub { font-size: 28px; letter-spacing: 6px; margin-top: 6px; }
</style>
</head>
<body>
  <section class="card card-front" aria-label="Business card front">
    <svg class="front-shapes" width="588" height="364" viewBox="0 0 588 364" aria-hidden="true">
      <polygon fill="var(--band-grey)" points="0,180 412,180 388,206 0,206"/>
      <polygon fill="var(--brand-red)" points="0,210 390,210 416,172 588,172 588,364 0,364"/>
    </svg>
    <div class="wordmark wordmark-front">
      <span class="name-main">VARNEX</span>
      <span class="name-sub">CONSULTING</span>
    </div>
    <ul class="contact-list">
      <li class="abn"><span><strong>ABN:</strong> 71203948865</span></li>
      <li><span>1300 485 193</span>
        <svg viewBox="0 0 24 24" aria-hidden="true"><path d="M6.6 10.8a15 15 0 0 0 6.6 6.6l2.2-2.2c.3-.3.7-.4 1-.2 1.1.4 2.3.6 3.6.6.6 0 1 .4 1 1V20c0 .6-.4 1-1 1A17 17 0 0 1 3 4c0-.6.4-1 1-1h3.5c.6 0 1 .4 1 1 0 1.3.2 2.5.6 3.6.1.3 0 .7-.2 1z"/></svg></li>
      <li><span>career@varnexconsulting.example</span>
        <svg viewBox="0 0 24 24" aria-hidden="true"><path d="M2 5h20v14H2z" fill="var(--card-white)"/><path d="M3 6l9 7 9-7" fill="none" stroke="var(--brand-red)" stroke-width="2"/></svg></li>
    </ul>
    <div class="person">
      <p class="person-name">Gavin Threlkeld</p>
      <p class="person-role">Principal</p>
      <address class="person-address">PO Box 3172 Merrowdale<br>NSW 2291</address>
    </div>
  </section>

  <section class="card card-back" aria-label="Business card back">
    <div class="wordmark wordmark-back">
      <span class="name-main">VARNEX</span>
      <span class="name-sub">CONSULTING</span>
    </div>
  </section>
</body>
</html>
```